Need a stunning home page for Car rental company

For a client, I need a slick and sumber home page design. It is a small, local car rental company, with a handful of cars available for rent.
Selling points: affordable lease, availability, always clean cars
The design should be:
- flat and modern
- no, or very few animations/sliders
- CTA: booking form for renting a car.
- 3 featured cars with images and facts (see website) with button to read more about the car.
- fullscreen background video can be an option
- main colour: #efba01
The site is under construction here:
http://solvikutleie.hammerlia.no/
Delivery requirements:
I need a layered & well organised PSD file delivered.

```html
<!DOCTYPE html>
<html lang="en">
<head>
<meta charset="utf-8">
<title>Solvik Bilutleie – Car Rental</title>
<link rel="stylesheet" href="https://fonts.googleapis.com/css2?family=Open+Sans:wght@400;600;700&display=swap">
<style>
:root{
  --gold:#ebb535;
  --gold-dark:#e2aa22;
  --gold-light:#f2c24a;
  --ink:#3c3c3c;
  --body:#555;
  --muted:#6b6b6b;
  --panel:#eeeeee;
  --dark:#333333;
  --white:#ffffff;
}
*{box-sizing:border-box;margin:0;padding:0}
html,body{width:1200px;height:2525px;overflow:hidden}
body{position:relative;background:var(--white);font-family:"Open Sans",Arial,sans-serif;color:var(--body)}
.abs{position:absolute}

/* header */
.site-header{left:0;top:0;width:1200px;height:118px}
.brand{left:131px;top:38px;font-size:34px;font-weight:700;letter-spacing:1px;color:var(--muted);text-transform:uppercase}
.call-us{right:131px;top:12px;font-size:22px;font-weight:700;color:var(--gold)}
.social{right:131px;top:60px;display:flex;gap:10px}
.social span{width:34px;height:34px;display:block}
.social .s1{background:#efb129}.social .s2{background:#3b5998}.social .s3{background:#3ea8e0}.social .s4{background:#e37aa6}

/* nav */
.main-nav{left:0;top:118px;width:1200px;height:86px;background:linear-gradient(#f2c23e,#e8b02a);display:flex;align-items:center;padding-left:131px}
.main-nav a{font-size:14.5px;color:#fff;text-decoration:none;text-transform:uppercase;margin-right:0}
.main-nav a.active{color:var(--ink)}

/* hero */
.hero{left:0;top:204px;width:1200px;height:449px;background:linear-gradient(180deg,#4a4b50 0%,#6d5a55 45%,#c77a4a 70%,#2b2623 100%)}
.hero-panel{left:722px;top:204px;width:347px;height:449px;background:rgba(25,22,20,.72);padding:34px 33px}
.hero-panel h1{font-size:26px;font-weight:700;color:var(--gold);text-transform:uppercase;margin-bottom:10px}
.hero-panel p{font-size:16.5px;line-height:32px;color:#fff}
.btn{display:inline-block;background:var(--gold);color:#fff;font-weight:700;text-transform:uppercase;text-align:center;border-radius:3px}
.hero-btn{left:757px;top:537px;width:184px;height:52px;line-height:52px;font-size:18px}
.dots{left:572px;top:601px;display:flex;gap:4px}
.dots i{width:14px;height:14px;border-radius:50%;border:2px solid #fff;background:#333;display:block}
.dots i.on{background:var(--gold-light)}

/* welcome */
.welcome{left:131px;top:688px;width:606px}
.section-title{font-size:28px;font-weight:700;color:var(--gold);text-transform:uppercase}
.welcome p{font-size:14.5px;line-height:25px;margin-top:14px;color:var(--body)}
.welcome .section-title{margin-bottom:2px}
.welcome-btn{left:131px;top:968px;width:169px;height:47px;line-height:47px;font-size:18px}

.search-box{left:786px;top:698px;width:283px;height:315px;background:var(--gold);padding:18px 20px}
.search-box h2{font-size:18px;font-weight:700;color:#fff;text-transform:uppercase;margin-bottom:14px}
.field{width:243px;height:37px;background:#fff;margin-bottom:12px;font-size:13px;color:#555;padding:0 11px;line-height:37px;position:relative}
.field svg{position:absolute;right:12px;top:15px}
.search-btn{width:118px;height:39px;line-height:39px;background:#555;color:#fff;font-weight:700;font-size:17px;text-align:center;text-transform:uppercase;margin-top:2px}

/* featured */
.featured{left:0;top:1060px;width:1200px;height:669px;background:var(--panel)}
.featured .section-title{position:absolute;left:129px;top:36px}
.car-card{top:1149px;width:289px;height:526px;background:#fff}
.car-photo{height:199px}
.car-body{padding:22px 22px 0}
.car-body h3{font-size:19px;font-weight:400;color:var(--gold);text-transform:uppercase}
.car-body p{font-size:14.5px;line-height:25px;margin-top:10px;padding-bottom:20px;border-bottom:1px solid #ddd}
.specs{margin-top:20px;font-size:14px;line-height:24.5px;width:100%;border-collapse:collapse}
.specs td:last-child{width:50px}
.card-btn{position:absolute;left:24px;bottom:31px;width:143px;height:44px;line-height:44px;font-size:18px}

/* video */
.video{left:0;top:1772px;width:1200px;height:428px;background:radial-gradient(ellipse at 45% 55%,#5a2a2c 0%,#3b3333 45%,#2e2e2e 100%)}
.play{left:556px;top:1933px}

/* footer */
.footer-col{top:2238px;font-size:14.5px;line-height:24.5px;color:var(--body)}
.footer-col h4{font-size:17.5px;font-weight:700;color:var(--gold);text-transform:uppercase;margin-bottom:10px}
.bottom-bar{left:0;top:2457px;width:1200px;height:68px;background:var(--dark);color:#fff;font-size:14.5px;line-height:68px;padding:0 131px}
.bottom-links{position:absolute;right:131px;top:0}
.bottom-links span{margin:0 21px}
</style>
</head>
<body>

<header class="site-header abs">
  <div class="brand abs">Solvik Bilutleie</div>
  <div class="call-us abs">Call Us : 91 23 45 67</div>
  <div class="social abs" aria-label="Social links">
    <span class="s1"></span><span class="s2"></span><span class="s3"></span><span class="s4"></span>
  </div>
</header>

<nav class="main-nav abs">
  <a class="active" href="#" style="margin-right:68px">Home</a>
  <a href="#" style="margin-right:67px">Services</a>
  <a href="#" style="margin-right:68px">The Fleet Our</a>
  <a href="#" style="margin-right:73px">Contact Us</a>
  <a href="#" style="margin-right:73px">Blog</a>
  <a href="#" style="margin-right:67px">Page Templates</a>
  <a href="#">About Us</a>
</nav>

<div class="hero abs" role="img" aria-label="Silver sports car driving on a road at sunset"></div>
<div class="hero-panel abs">
  <h1>Solvik Bilutleie</h1>
  <p>Lorem ipsum dolor sit amet, nec id wisi latine. Eos vero incorrupte te. Ut sint erat posse mei. Qui simul aperiam at. Duo error adipisci sad-ipscing in, no purto patrique quo. Principes delicatissimi vis id.purto patrique quo. Principes...</p>
</div>
<a class="btn hero-btn abs">Booking Form</a>
<div class="dots abs"><i class="on"></i><i></i><i></i></div>

<section class="welcome abs">
  <h2 class="section-title">Welcome to Solvik Bilutleie</h2>
  <p>Sit autem lobortis ut, accusam facilisi et vix, nam ne tibique dissentiunt. Illum ignota pro te. Quot impetus pertinax nec cu. Mel ut tamquam facilis incorrupte. Ponderum pertina-cia in vel, ne mei pericula intellegat. Per ullum mediocritatem at, vel ei legere gloriatur, corpora legendos mei ea.</p>
  <p>Sit autem lobortis ut, accusam facilisi et vix, nam ne tibique dissentiunt. Illum ignota pro te. Quot impetus pertinax nec cu. Mel ut tamquam facilis incorrupte. Ponderum pertina-cia in vel, ne mei pericula intellegat. Per ullum mediocritatem.Per ullum mediocritatem at, vel ei legere gloriatur, corpora legendos mei ea.</p>
</section>
<a class="btn welcome-btn abs">Read More</a>

<form class="search-box abs">
  <h2>Search and Book</h2>
  <div class="field">Car type<svg width="8" height="5" viewBox="0 0 8 5"><path d="M0 0h8L4 5z" fill="#888"/></svg></div>
  <div class="field">Car model<svg width="8" height="5" viewBox="0 0 8 5"><path d="M0 0h8L4 5z" fill="#888"/></svg></div>
  <div class="field">Name</div>
  <div class="field">Email</div>
  <div class="search-btn">Search</div>
</form>

<section class="featured abs">
  <h2 class="section-title">Featured Cars</h2>
</section>

<article class="car-card abs" style="left:131px">
  <div class="car-photo" role="img" aria-label="Red sports coupe in a grey studio" style="background:linear-gradient(#e6e6e6,#9a9a9a)"></div>
  <div class="car-body">
    <h3>Lorem ipsum dolor</h3>
    <p>Lorem ipsum dolor sit amet, nec id wisi latine. Eos vero incorrupte te.</p>
    <table class="specs"><tr><td>Bill type</td><td>Varebil</td></tr><tr><td>Max. pers</td><td>22</td></tr><tr><td>Girtype manual</td><td>Yes</td></tr></table>
  </div>
  <a class="btn card-btn">Read More</a>
</article>
<article class="car-card abs" style="left:454px">
  <div class="car-photo" role="img" aria-label="Black luxury sports car" style="background:linear-gradient(#4a4a4a,#1e1e1e)"></div>
  <div class="car-body">
    <h3>Lorem ipsum dolor</h3>
    <p>Lorem ipsum dolor sit amet, nec id wisi latine. Eos vero incorrupte te.</p>
    <table class="specs"><tr><td>Bill type</td><td>Varebil</td></tr><tr><td>Max. pers</td><td>22</td></tr><tr><td>Girtype manual</td><td>Yes</td></tr></table>
  </div>
  <a class="btn card-btn">Read More</a>
</article>
<article class="car-card abs" style="left:780px">
  <div class="car-photo" role="img" aria-label="Grey supercar under a cloudy sky" style="background:linear-gradient(#5a6068,#3a3c40)"></div>
  <div class="car-body">
    <h3>Lorem ipsum dolor</h3>
    <p>Lorem ipsum dolor sit amet, nec id wisi latine. Eos vero incorrupte te.</p>
    <table class="specs"><tr><td>Bill type</td><td>Varebil</td></tr><tr><td>Max. pers</td><td>22</td></tr><tr><td>Girtype manual</td><td>Yes</td></tr></table>
  </div>
  <a class="btn card-btn">Read More</a>
</article>

<div class="video abs" role="img" aria-label="Video still of a red coupe driving, dimmed"></div>
<svg class="play abs" width="90" height="90" viewBox="0 0 90 90" aria-label="Play video">
  <circle cx="45" cy="45" r="42" fill="none" stroke="#fff" stroke-width="4"/>
  <path d="M36 27 L63 45 L36 63 Z" fill="#fff"/>
</svg>

<footer>
  <div class="footer-col abs" style="left:131px;width:220px">
    <h4>About Us</h4>
    Lorem ipsum dolor sit amet,<br>nec id wisi latine. Eos vero<br>incorrupte te. Ut sint erat<br>posse mei. Qui simul aperiam<br>at. ui simul aperiam.Qui simul<br>aperiam at. ui simul aperiam.
  </div>
  <div class="footer-col abs" style="left:404px">
    <h4>Special Offers</h4>
    Elit sed do eiusmod tem<br>Incididunt ut labore<br>Et dolore magna aliqua<br>Ut enim ad minim veniam<br>Quis nostrud exercitation
  </div>
  <div class="footer-col abs" style="left:653px">
    <h4>Partners</h4>
    Et dolore magna aliqua<br>Ut enim ad minim veniam<br>Quis nostrud exercitation<br>Lorem ipsum dolor<br>Conse ctetur adipisicing<br>Elit sed do eiusmod
  </div>
  <div class="footer-col abs" style="left:891px">
    <h4>Services</h4>
    Et dolore magna aliqua<br>Ut enim ad minim veniam<br>Quis nostrud exercitation<br>Lorem ipsum dolor<br>Conse ctetur adipisicing<br>Elit sed do eiusmod
  </div>
  <div class="bottom-bar abs">
    Copyright @ 2014 Solvik Bilutleie.All Rights Reserved.
    <div class="bottom-links">Home<span>|</span>Configure</div>
  </div>
</footer>

</body>
</html>
```